Psychiatric Office Needs a Website- 1st Time Ever!

Been in practice since 2003 with no website, but finally ready to dive in. We are Maplecrest Behavioral Healthcare, a mental health outpatient practice based in Fayetteville, Georgia that sees diverse individuals and families from childhood to advanced age for a variety of conditions. We've grown by word of mouth and referral but would now like to have a digital footprint. Be the pioneer of our website and we will be sure to share. We would like to see designs that are modern, animated, fairly colorful, easy to read, and caters to all ages. Also, we would like the design to take the whole page (not be centered) and can be viewed well on phone/tablet. Please see our outline for more information. Our motto/slogan is: Maplecrest Behavioral Healthcare- A step forward in your wellness journey, so the design should try to reflect that.
Updates

Project Deadline Extended
Reason: site in progress

Target Market(s)

Children through elderly

Industry/Entity Type

Medical

Logo Text

Stepping forward in your wellness journey

Number of Pages Required

1 page

Colors

Designer to choose colors to be used in the design.

Requirements
Must have
• Animation or moving pictures.
• Color.
• Concise.
• User friendly
• Diversity in the stock photos

```html
<!DOCTYPE html>
<html lang="en">
<head>
<meta charset="utf-8">
<title>Maplecrest Behavioral Healthcare</title>
<link href="https://fonts.googleapis.com/css2?family=Nunito+Sans:wght@300;400;600;700&display=swap" rel="stylesheet">
<style>
:root{
  --blue:#29aae1;
  --blue-dark:#1d8fc4;
  --orange:#f7941d;
  --ink:#333;
  --muted:#777;
  --soft:#f4f4f4;
  --line:#dcdcdc;
  --white:#fff;
}
*{margin:0;padding:0;box-sizing:border-box}
html,body{width:1200px;height:3523px;overflow:hidden}
body{font-family:"Nunito Sans",Arial,sans-serif;color:var(--ink);background:var(--white);position:relative}
section,header,nav,footer{position:relative;width:1200px}

/* header */
.site-header{height:160px}
.brand{position:absolute;left:99px;top:30px;display:flex;align-items:center;gap:14px}
.brand-dot{width:70px;height:70px;border-radius:50%;background:var(--blue)}
.brand-text{font-weight:700;font-size:19px;color:var(--blue);line-height:1.2;width:150px}
.brand-tag{position:absolute;left:99px;top:126px;font-size:11px;color:var(--ink)}
.info{position:absolute;top:66px;display:flex;align-items:center;gap:14px;font-size:13px;line-height:1.5}
.info b{font-weight:700}
.info-icon{width:46px;height:46px;border-radius:50%;background:var(--blue);display:flex;align-items:center;justify-content:center}
.info-hours{left:432px}
.info-contact{left:704px}
.portal-btn{position:absolute;left:939px;top:73px;width:162px;height:42px;background:var(--orange);color:var(--white);font-size:15px;font-weight:600;display:flex;align-items:center;justify-content:center;letter-spacing:.5px}

/* nav */
.main-nav{height:47px;background:var(--blue);display:flex;padding-left:99px}
.main-nav a{color:var(--white);text-decoration:none;font-size:15px;display:flex;align-items:center;padding:0 19px;height:47px}
.main-nav a.active{background:var(--orange)}
.nav-search{position:absolute;right:99px;top:15px}

/* hero */
.hero{height:502px;overflow:hidden}
.hero-photo{position:absolute;inset:0;background:
  radial-gradient(ellipse 55% 45% at 62% 88%,#f4f4f4 0%,#dcdcdc 35%,rgba(200,200,200,0) 70%),
  radial-gradient(ellipse 40% 60% at 8% 70%,#ececec 0%,rgba(220,220,220,0) 70%),
  linear-gradient(100deg,#9a9a9a 0%,#c8c8c8 30%,#8d8d8d 55%,#b4b4b4 75%,#7b7b7b 100%)}
.hero-content{position:absolute;left:0;right:0;top:118px;text-align:center;color:var(--white)}
.hero-title{font-size:56px;font-weight:700;text-shadow:0 2px 6px rgba(0,0,0,.35)}
.hero-sub{font-size:34px;font-weight:300;margin-top:2px;text-shadow:0 2px 6px rgba(0,0,0,.35)}
.hero-btn{display:inline-block;margin-top:26px;width:246px;height:52px;line-height:52px;background:var(--blue);font-size:21px;font-weight:600;letter-spacing:.5px}
.hero-arrow{position:absolute;top:222px;width:46px;height:46px;border-radius:50%;background:rgba(255,255,255,.25);display:flex;align-items:center;justify-content:center}

/* welcome */
.welcome{height:437px;text-align:center}
.section-title{font-weight:300;font-size:34px;color:#555;letter-spacing:.5px}
.welcome .section-title{color:var(--blue);padding-top:72px;font-weight:400;font-size:33px}
.welcome p{font-size:13px;line-height:21px;color:var(--muted);width:904px;margin:20px auto 0}
.outline-btn{display:inline-block;border:2px solid var(--blue);color:var(--blue);font-weight:600;letter-spacing:.5px}
.welcome .outline-btn{margin-top:42px;width:284px;height:49px;line-height:45px;font-size:17px}

/* services */
.services{height:650px;background:var(--soft);text-align:center}
.services .section-title{padding-top:54px}
.service-grid{position:absolute;left:99px;top:143px;display:flex;gap:22px}
.service-card{width:234px;height:348px;background:var(--white);text-align:left}
.service-photo{height:181px}
.service-card h3{font-weight:400;font-size:17px;line-height:21px;color:#555;padding:18px 18px 0;height:62px}
.service-card p{font-size:11.5px;line-height:17px;color:var(--muted);padding:10px 18px 0}
.services .outline-btn{position:absolute;left:519px;top:538px;width:162px;height:38px;line-height:34px;font-size:16px;font-weight:400}

/* faq */
.faq{height:477px;overflow:hidden;background:linear-gradient(180deg,#2eaee4,#249fd6);color:var(--white)}
.faq .section-title{color:var(--white);text-align:center;padding-top:62px}
.faq-art{position:absolute;left:680px;top:120px;width:330px;height:330px;border-radius:10px;background:radial-gradient(ellipse at 55% 55%,rgba(20,110,160,.35) 0%,rgba(255,255,255,.14) 45%,rgba(255,255,255,.04) 100%);transform:rotate(-14deg)}
.faq-list{position:absolute;left:164px;top:168px}
.faq-item{margin-bottom:34px}
.faq-q{font-weight:700;font-size:18px}
.faq-a{font-size:13px;margin-top:12px;opacity:.92}

/* news */
.news{height:585px;text-align:center}
.news .section-title{padding-top:60px}
.news-intro{font-size:13px;line-height:22px;color:var(--muted);width:820px;margin:24px auto 0}
.news-grid{position:absolute;left:101px;top:235px;display:flex;gap:37px;text-align:left}
.news-card{width:308px}
.news-photo{height:157px}
.news-card h3{font-weight:700;font-size:18px;margin-top:22px}
.news-card p{font-size:11.5px;line-height:16px;color:#555;margin-top:10px}
.news-card time{display:block;font-size:14px;margin-top:12px;padding-left:4px}

/* contact */
.contact{height:594px;background:var(--soft)}
.contact .section-title{text-align:center;padding-top:58px}
.contact-info{position:absolute;left:99px;top:172px;font-size:18px;line-height:26px}
.contact-row{display:flex;gap:10px;margin-bottom:16px}
.contact-row svg{flex:none;margin-top:5px}
.contact-row b{font-weight:700}
.social-dot{width:36px;height:36px;border-radius:50%;background:var(--blue);margin-top:12px}
.contact-form{position:absolute;left:547px;top:166px;width:554px}
.field{background:var(--white);border:1px solid var(--line);height:40px;font-size:11px;color:#aaa;padding:12px 14px;margin-bottom:19px}
.field-row{display:flex;gap:28px}
.field-row .field{flex:1}
.field-msg{height:94px}
.submit-btn{width:125px;height:38px;background:var(--orange);color:var(--white);font-size:14px;display:flex;align-items:center;justify-content:center;margin-top:18px}

/* footer */
.site-footer{height:71px;background:var(--blue);color:var(--white);font-size:13px;display:flex;align-items:center;justify-content:center}
.footer-mark{position:absolute;right:42px;top:28px;font-size:11px;opacity:.8}
</style>
</head>
<body>

<header class="site-header">
  <div class="brand">
    <div class="brand-dot"></div>
    <div class="brand-text">Maplecrest Behavioral Healthcare</div>
  </div>
  <div class="brand-tag">A step forward in your wellness journey</div>

  <div class="info info-hours">
    <div class="info-icon"><svg width="22" height="22" viewBox="0 0 22 22"><circle cx="11" cy="11" r="9" fill="none" stroke="#fff" stroke-width="2"/><path d="M11 6v5l3 2" stroke="#fff" stroke-width="2" fill="none"/></svg></div>
    <div><b>Monday-Friday: 9am to 5pm</b><br>Saturday / Sunday: Closed</div>
  </div>
  <div class="info info-contact">
    <div class="info-icon"><svg width="20" height="20" viewBox="0 0 20 20"><path d="M4 2l3 0 2 5-2 1.5a11 11 0 0 0 4.5 4.5L13 11l5 2v3a2 2 0 0 1-2 2A14 14 0 0 1 2 4a2 2 0 0 1 2-2z" fill="#fff"/></svg></div>
    <div><b>+1 770 555 0143</b><br>hello@maplecrestbh.com</div>
  </div>
  <div class="portal-btn">PATIENT PORTAL</div>
</header>

<nav class="main-nav">
  <a class="active">HOME</a>
  <a>ABOUT US</a>
  <a>SERVICES</a>
  <a>CONDITIONS WE TREAT</a>
  <a>NEW PATIENTS</a>
  <a>CONTACT US</a>
  <svg class="nav-search" width="16" height="16" viewBox="0 0 16 16"><circle cx="6.5" cy="6.5" r="5" fill="none" stroke="#fff" stroke-width="2"/><path d="M10.5 10.5l4 4" stroke="#fff" stroke-width="2.2"/></svg>
</nav>

<section class="hero">
  <div class="hero-photo" role="img" aria-label="Black and white photo of a caregiver's hands gently holding a patient's hand"></div>
  <div class="hero-arrow" style="left:26px"><svg width="14" height="20" viewBox="0 0 14 20"><path d="M10 3L4 10l6 7" stroke="#fff" stroke-width="2" fill="none"/></svg></div>
  <div class="hero-arrow" style="right:26px"><svg width="14" height="20" viewBox="0 0 14 20"><path d="M4 3l6 7-6 7" stroke="#fff" stroke-width="2" fill="none"/></svg></div>
  <div class="hero-content">
    <h1 class="hero-title">Maplecrest Behavioral Healthcare</h1>
    <p class="hero-sub">A step forward in your wellness journey</p>
    <span class="hero-btn">TAKE A SCREENING</span>
  </div>
</section>

<section class="welcome">
  <h2 class="section-title">WELCOME TO MAPLECREST BEHAVIORAL HEALTHCARE</h2>
  <p>Nemo enim ipsam voluptatem quia voluptas sit aspernatur aut odit aut fugit, sed quia consequuntur magni dolores eos qui ratione voluptatem sequi nesciunt. Neque porro quisquam est, qui dolorem ipsum quia dolor sit amet, consectetur, adipisci velit, sed quia non numquam eius modi tempora incidunt ut labore et dolore magnam aliquam quaerat voluptatem.</p>
  <p>Ut enim ad minima veniam, quis nostrum exercitationem ullam corporis suscipit laboriosam, nisi ut aliquid ex ea commodi consequatur? Quis autem vel eum iure reprehenderit qui in ea voluptate velit esse quam nihil molestiae consequatur, vel illum qui dolorem eum fugiat.</p>
  <span class="outline-btn">READ MORE INFORMATION</span>
</section>

<section class="services">
  <h2 class="section-title">OUR SERVICES</h2>
  <div class="service-grid">
    <article class="service-card">
      <div class="service-photo" role="img" aria-label="Photo of a clinician checking a patient's blood pressure" style="background:linear-gradient(160deg,#f7f9fb 0%,#dfe8ef 35%,#f1d9c9 60%,#c4d2dd 100%)"></div>
      <h3>Diagnostic Evaluation and Treatment</h3>
      <p>Sed do eiusmod tempor incididunt ut labore et dolore magna aliqua quis nostrud exercitation ullamco laboris nisi ut aliquip.</p>
    </article>
    <article class="service-card">
      <div class="service-photo" role="img" aria-label="Photo of a doctor speaking with a patient resting in bed" style="background:linear-gradient(120deg,#e8e6e3 0%,#fafafa 30%,#d7c3b3 50%,#f2f2f2 70%,#b9c1c8 100%)"></div>
      <h3>Substance Abuse Assessments</h3>
      <p>Sed do eiusmod tempor incididunt ut labore et dolore magna aliqua quis nostrud exercitation ullamco laboris nisi ut aliquip.</p>
    </article>
    <article class="service-card">
      <div class="service-photo" role="img" aria-label="Photo of a counselor in consultation with a client" style="background:linear-gradient(110deg,#ecebe8 0%,#b7b3ac 30%,#8d8a85 55%,#c9c6c0 75%,#6f6c68 100%)"></div>
      <h3>Bariatric Pre-surgical Consultation</h3>
      <p>Sed do eiusmod tempor incididunt ut labore et dolore magna aliqua quis nostrud exercitation ullamco laboris nisi ut aliquip.</p>
    </article>
    <article class="service-card">
      <div class="service-photo" role="img" aria-label="Photo of a mother and child meeting with a pediatric specialist" style="background:linear-gradient(120deg,#f6efe4 0%,#e9c9a4 30%,#f3e6d6 55%,#d8b591 75%,#b7c7d6 100%)"></div>
      <h3>Early Childhood Assessments</h3>
      <p>Sed do eiusmod tempor incididunt ut labore et dolore magna aliqua quis nostrud exercitation ullamco laboris nisi ut aliquip.</p>
    </article>
  </div>
  <span class="outline-btn">VIEW MORE</span>
</section>

<section class="faq">
  <div class="faq-art" role="img" aria-label="Faded photo of paper cards with a question mark"></div>
  <h2 class="section-title">FAQS</h2>
  <div class="faq-list">
    <div class="faq-item"><p class="faq-q">Q. What do I need to bring with me to my first visit?</p><p class="faq-a">A- Insurance card, patient forms found on our Form's page.</p></div>
    <div class="faq-item"><p class="faq-q">Q- How long do I have to wait to be seen?</p><p class="faq-a">A- We try to have very little wait time for your convenience.</p></div>
    <div class="faq-item"><p class="faq-q">Q- What types of insurance do you accept?</p><p class="faq-a">A- We accept a large variety of insurance plans.</p></div>
  </div>
</section>

<section class="news">
  <h2 class="section-title">LATEST NEWS</h2>
  <p class="news-intro">At vero eos et accusamus et iusto odio dignissimos ducimus qui blanditiis praesentium voluptatum deleniti atque corrupti quos dolores et quas molestias.</p>
  <div class="news-grid">
    <article class="news-card">
      <div class="news-photo" role="img" aria-label="Photo of a worried woman being comforted by a counselor" style="background:linear-gradient(110deg,#f3f4f6 0%,#e4c9b4 25%,#d9dde2 45%,#f6f6f7 65%,#9fb0bf 100%)"></div>
      <h3>Numquam Eius Modi Tempora</h3>
      <p>Class aptent taciti sociosqu ad litora torquent per co nubia nostra per inceptos hymenaeos.</p>
      <time>25 FEB 2017</time>
    </article>
    <article class="news-card">
      <div class="news-photo" role="img" aria-label="Photo of three generations of women smiling together" style="background:linear-gradient(110deg,#c7b29c 0%,#ead8c3 25%,#b08a69 50%,#e8cfb4 72%,#8f7560 100%)"></div>
      <h3>Occaecat Cupidatat Proident</h3>
      <p>Class aptent taciti sociosqu ad litora torquent per co nubia nostra per inceptos hymenaeos.</p>
      <time>25 FEB 2017</time>
    </article>
    <article class="news-card">
      <div class="news-photo" role="img" aria-label="Photo of a smiling senior woman with a caregiver" style="background:linear-gradient(110deg,#f4f5f6 0%,#dde6ee 30%,#f0e2d6 55%,#6f9cc4 80%,#d6dee6 100%)"></div>
      <h3>Officia Deserunt Mollit Anim</h3>
      <p>Class aptent taciti sociosqu ad litora torquent per co nubia nostra per inceptos hymenaeos.</p>
      <time>25 FEB 2017</time>
    </article>
  </div>
</section>

<section class="contact">
  <h2 class="section-title">CONTACT US</h2>
  <div class="contact-info">
    <div class="contact-row"><svg width="14" height="18" viewBox="0 0 14 18"><path d="M7 0a7 7 0 0 1 7 7c0 5-7 11-7 11S0 12 0 7a7 7 0 0 1 7-7z" fill="#29aae1"/><circle cx="7" cy="7" r="2.5" fill="#fff"/></svg><div><b>Address:</b> No, Street Name, City Address<br>Country, Code.</div></div>
    <div class="contact-row"><svg width="16" height="16" viewBox="0 0 20 20"><path d="M4 2l3 0 2 5-2 1.5a11 11 0 0 0 4.5 4.5L13 11l5 2v3a2 2 0 0 1-2 2A14 14 0 0 1 2 4a2 2 0 0 1 2-2z" fill="#29aae1"/></svg><div><b>Call Us:</b> +1 770 555 0143</div></div>
    <div class="contact-row"><svg width="18" height="14" viewBox="0 0 18 14"><rect x="1" y="1" width="16" height="12" fill="none" stroke="#29aae1" stroke-width="1.6"/><path d="M1 1l8 7 8-7" fill="none" stroke="#29aae1" stroke-width="1.6"/></svg><div><b>Email:</b> hello@maplecrestbh.com</div></div>
    <div class="social-dot" role="img" aria-label="Social profile link"></div>
  </div>
  <div class="contact-form">
    <div class="field-row"><div class="field">First Name *</div><div class="field">Last Name *</div></div>
    <div class="field">Email *</div>
    <div class="field-row"><div class="field">Phone Number *</div><div class="field">Company Name</div></div>
    <div class="field field-msg">How can we help *</div>
    <div class="submit-btn">SUBMIT NOW</div>
  </div>
</section>

<footer class="site-footer">
  © 2017 MBHC. All right reserved. Term of Use
  <span class="footer-mark">C18</span>
</footer>

</body>
</html>
```